The Q Collective Business Cards

We need a sleek looking business card for our real estate company. Looking for a clean, modern, eye catching design on a standard size business card.
Updates

No more submissions please! Thank you!

Target Market(s)

General Public/Real Estate Clients

Industry/Entity Type

Real Estate

Contact Information for Business Card

Cards will be customized for each agent.

Colors

Designer to choose only greyscale colors for use in the design.

Requirements
Must have
• Black, white, gray color pallet, Photo area for headshot on the front of the card

```html
<!DOCTYPE html>
<html lang="en">
<head>
<meta charset="utf-8">
<title>The Q Collective – Business Card</title>
<link rel="stylesheet" href="https://fonts.googleapis.com/css2?family=Montserrat:wght@400;500&family=Roboto:wght@400;500&display=swap">
<style>
  :root {
    --page-bg: #d8d3cc;
    --card-light: #eeece9;
    --card-mid: #dcd8d3;
    --ink: #1c1c1c;
    --band: #6b6866;
    --band-name: #f1ece4;
    --band-title: #e2ddd6;
    --photo-warm: #c9b3a3;
    --photo-light: #e6ddd3;
    --photo-deep: #8c6e5c;
  }
  html, body {
    margin: 0;
    width: 1200px;
    height: 1054px;
    overflow: hidden;
    background: var(--page-bg);
  }
  .card {
    position: absolute;
    left: 100px;
    top: 227px;
    width: 1000px;
    height: 600px;
    border-radius: 28px;
    overflow: hidden;
    background: linear-gradient(135deg, var(--card-light), var(--card-mid));
    box-shadow: 0 18px 40px rgba(0,0,0,0.18);
    font-family: "Roboto", Arial, sans-serif;
    color: var(--ink);
  }
  .headshot {
    position: absolute;
    left: 0; top: 0;
    width: 477px; height: 600px;
    background: radial-gradient(ellipse at 45% 40%, var(--photo-light) 0%, var(--photo-warm) 55%, var(--photo-deep) 100%);
  }
  .brand {
    position: absolute;
    left: 518px; top: 61px;
    width: 415px; height: 85px;
    display: flex;
    align-items: center;
    justify-content: center;
    gap: 16px;
    font-family: "Montserrat", Arial, sans-serif;
    font-weight: 500;
    font-size: 40px;
    color: var(--ink);
  }
  .brand-mark {
    width: 18px; height: 18px;
    background: var(--ink);
  }
  .name-band {
    position: absolute;
    left: 449px; top: 230px;
    width: 551px; height: 102px;
    background: var(--band);
    box-sizing: border-box;
    padding: 12px 0 0 69px;
  }
  .agent-name {
    font-family: "Montserrat", Arial, sans-serif;
    font-weight: 500;
    font-size: 40px;
    line-height: 48px;
    color: var(--band-name);
  }
  .agent-title {
    font-size: 24px;
    line-height: 30px;
    color: var(--band-title);
  }
  .address {
    position: absolute;
    left: 518px; top: 350px;
    font-size: 25px;
    line-height: 38px;
  }
  .contacts {
    position: absolute;
    left: 518px; top: 434px;
    margin: 0; padding: 0;
    list-style: none;
    font-size: 25px;
    line-height: 38px;
  }
  .contacts li {
    display: flex;
    align-items: center;
    gap: 24px;
  }
  .contacts svg {
    width: 24px; height: 24px;
    fill: var(--ink);
    flex: none;
  }
</style>
</head>
<body>
  <div class="card">
    <div class="headshot" role="img" aria-label="Agent headshot photo"></div>

    <div class="brand">
      <span class="brand-mark"></span>
      <span class="brand-name">The Q Collective</span>
    </div>

    <div class="name-band">
      <div class="agent-name">Nora Castillo Bennett</div>
      <div class="agent-title">Real Estate Broker</div>
    </div>

    <div class="address">
      <div>4120 Magnolia Ave</div>
      <div>Riverton, LA, US 70999</div>
    </div>

    <ul class="contacts">
      <li>
        <svg viewBox="0 0 24 24" aria-hidden="true"><path d="M3 8c0-2 2-4 9-4s9 2 9 4v2h-5V8H8v2H3z"/><rect x="5" y="11" width="14" height="9" rx="1.5"/></svg>
        <span>+1 555-014-2297</span>
      </li>
      <li>
        <svg viewBox="0 0 24 24" aria-hidden="true"><path d="M2 5h20v14H2z M4 7v1l8 5 8-5V7l-8 5z" fill-rule="evenodd"/></svg>
        <span>nora@homefindernest.com</span>
      </li>
      <li>
        <svg viewBox="0 0 24 24" aria-hidden="true"><path d="M12 2a10 10 0 1 0 0 20 10 10 0 0 0 0-20zm-1 2.1V8H7.6A8 8 0 0 1 11 4.1zM13 4.1A8 8 0 0 1 16.4 8H13zM4.3 10H11v4H4.3a8 8 0 0 1 0-4zM13 10h6.7a8 8 0 0 1 0 4H13zM7.6 16H11v3.9A8 8 0 0 1 7.6 16zM13 16h3.4A8 8 0 0 1 13 19.9z"/></svg>
        <span>www.homefindernest.com</span>
      </li>
    </ul>
  </div>
</body>
</html>
```